South Florida Real Estate Brokerage Business

The name is LAKE VORISSA REAL ESTATE.
The company is a Real estate realty based in Miami.
Is targeted to Latin American clients.
Must express luxury, and efficiency.
Target clients for properties around 250k to a million +.
Vorissa means Royal in Latin.
Should communicate safety and knowledge of the product and transaction with a tech edge.

The web design needs to be a Social tool, with Friendloop and other media integration of some sort. Needs to have a Show case place, a Search place (MLS listings) with maps and filters.
Needs to reflect luxury but also mixed with a social edge capable of engaging clients or transition them to communicate with the page.
Include the logo from the uploaded files, feel free to change the color or font per webdesign.
This is a Front en design, layout and graphics.
Possible future programming if approved.
I can receive Quotes for the Code part.

Spanish and English speakers living in Latin America and Canada looking for apartments and houses to buy.

Business

• Search area.
Neighbourhood area.
Could be a blog or news area.
Client registration.
Social Plugin
• Social linking to networks.
Log in with friendloop account.
Friendloop Like.

```html
<!DOCTYPE html>
<html lang="en">
<head>
<meta charset="utf-8">
<title>Lake Vorissa Real Estate — Properties</title>
<link rel="stylesheet" href="https://fonts.googleapis.com/css2?family=Archivo+Narrow:wght@400;500&family=Noto+Sans:wght@400;700&display=swap">
<style>
:root{
  --slate:#4a525d;
  --slate-dark:#3f4650;
  --gold:#d3ac62;
  --gold-light:#ede0c6;
  --gold-text:#c9a15a;
  --ink:#3b3b3b;
  --muted:#8a8a8a;
  --white:#ffffff;
  --black:#111111;
  --badge-dark:#4a525d;
}
*{box-sizing:border-box;margin:0;padding:0}
html,body{width:1000px;height:1200px;overflow:hidden}
body{position:relative;background:var(--slate);font-family:"Noto Sans",Verdana,sans-serif;color:var(--white)}
.abs{position:absolute}
.topline{left:0;top:0;width:1000px;height:3px;background:var(--gold)}
.narrow{font-family:"Archivo Narrow","Arial Narrow",sans-serif}

/* header */
.brand{left:118px;top:28px;width:140px;text-align:center}
.brand-mark{display:block;width:26px;height:26px;margin:0 auto 8px;border:2px solid var(--gold)}
.brand-name{font-family:"Archivo Narrow",sans-serif;color:var(--gold);font-size:13px;line-height:15px;letter-spacing:1px}
.tagline{left:88px;top:96px;font-size:17px;letter-spacing:1px;font-family:"Archivo Narrow",sans-serif}
.account{right:68px;top:14px;display:flex;align-items:center;gap:6px;font-size:11px;letter-spacing:1px}
.fl-login{display:flex;align-items:center;gap:4px;background:#5b6f9c;padding:2px 6px;font-size:9px;font-weight:700;letter-spacing:0;margin-left:6px}
.fl-login i{width:9px;height:9px;background:var(--white);display:block}
.mainnav{right:68px;top:94px;display:flex;gap:21px;font-family:"Archivo Narrow",sans-serif;font-size:14px;letter-spacing:1px}

/* page panel */
.panel{left:88px;top:125px;width:844px;height:856px;background:var(--white)}
.sidebar{left:108px;top:145px;width:210px;height:815px;background:var(--gold);box-shadow:3px 0 4px rgba(0,0,0,.15)}
.map{left:122px;top:158px;width:181px;height:178px;border:3px solid #e6d2a8;background:linear-gradient(135deg,#e9e6dc,#dfe6d8 60%,#e8dcd0)}
.side-rule{left:108px;height:2px;width:210px;background:#c49c52}
.side-label{left:122px;font-family:"Archivo Narrow",sans-serif;font-size:14px;letter-spacing:.5px}
.select{height:24px;background:var(--white);border:1px solid #c9a65e;color:#666;font-size:11px;padding:5px 8px;display:flex;justify-content:space-between;align-items:center}
.select svg{width:10px;height:9px}
.btn-black{left:122px;width:181px;height:24px;background:var(--black);color:var(--white);font-size:11px;font-weight:700;letter-spacing:1px;text-align:center;line-height:24px}
.hoods{left:122px;top:619px;list-style:none;font-size:11px;color:#2f2f2f;letter-spacing:.5px}
.hoods li{display:flex;align-items:center;gap:6px;height:16.7px}
.hoods .box{width:9px;height:9px;border:1px solid #6c7a8a;background:#f4f4f4;display:flex;align-items:center;justify-content:center}

/* listing toolbar */
.toolbar{left:338px;width:574px;height:25px;background:var(--gold-light);color:#555;font-size:10px;display:flex;align-items:center;padding:0 4px}
.tb-select{height:14px;background:var(--white);border:1px solid #c9c9c9;font-size:8px;color:#555;padding:0 3px;display:flex;align-items:center;justify-content:space-between;margin:0 16px 0 8px}
.tb-select b{width:12px;height:12px;background:#c9d6ea;display:block}
.pager{margin-left:auto;display:flex;align-items:center;gap:7px;margin-right:6px}
.pager svg{width:8px;height:11px}

/* listings */
.listing{left:338px;width:574px;height:171px;border-bottom:1px solid #e4e4e4}
.photo{position:absolute;left:0;top:0;width:148px;height:148px;border:2px solid #dcdcdc;background:linear-gradient(180deg,#e8ecef 0%,#d9dfe4 55%,#b9b5b0 100%)}
.title{position:absolute;left:163px;top:-4px;font-family:"Archivo Narrow",sans-serif;font-size:18px;color:var(--ink)}
.price{position:absolute;right:0;top:-4px;font-family:"Archivo Narrow",sans-serif;font-size:21px;color:var(--gold-text)}
.addr{position:absolute;left:163px;top:22px;font-size:10.5px;font-weight:700;color:#777;letter-spacing:.5px}
.desc{position:absolute;left:163px;top:46px;width:411px;font-size:10px;line-height:15px;color:#8e8e8e;text-align:justify;letter-spacing:.4px}
.badges{position:absolute;left:163px;top:128px;display:flex;gap:8px}
.badge{width:54px;height:19px;background:var(--gold);display:flex;align-items:center;gap:4px;padding-left:9px;font-size:11px;color:var(--white)}
.badge svg{width:24px;height:10px}
.badge.view{background:var(--badge-dark);justify-content:center;padding:0;font-weight:700;letter-spacing:1px;margin-left:-0px}

/* footer */
.footnav{left:88px;top:1010px;display:flex;font-size:11px;letter-spacing:1px}
.footnav span+span::before{content:"|";color:var(--gold);margin:0 6px}
.social{top:1002px;width:30px;height:30px;background:var(--slate-dark);color:#d8d8d8;font-size:6.5px;display:flex;align-items:center;justify-content:center;text-align:center}
.rule{left:0;width:1000px;height:1px;background:#5c646f}
.rule.short{left:88px;width:845px}
.fcol{top:1062px;font-size:11px;line-height:15px;letter-spacing:1px}
.news-title{left:433px;top:1058px;font-family:"Archivo Narrow",sans-serif;font-size:18px;letter-spacing:.5px}
.news-box{left:433px;top:1085px;width:228px;height:59px;background:linear-gradient(180deg,#646b75,#555d68);padding:6px 7px;font-size:11px;line-height:15px;letter-spacing:.5px}
.readmore{display:inline-block;margin-top:3px;background:var(--gold);font-size:9px;font-weight:700;padding:0 6px;letter-spacing:1px}
.arrow{top:1103px;width:9px;height:12px}
.nl-title{right:67px;top:1058px;font-family:"Archivo Narrow",sans-serif;font-size:18px;letter-spacing:1px}
.input{height:25px;background:var(--white);color:#888;font-size:11px;padding:6px 7px}
.submit{left:880px;top:1118px;width:53px;height:25px;background:var(--gold);font-size:11px;font-weight:700;text-align:center;line-height:25px}
.copy{left:88px;top:1180px;font-size:11px;color:#9aa0a8;letter-spacing:1px}
</style>
</head>
<body>
<div class="abs topline"></div>

<header>
  <div class="abs brand">
    <span class="brand-mark"></span>
    <div class="brand-name">LAKE VORISSA<br>REAL ESTATE</div>
  </div>
  <div class="abs tagline">South Florida Real estate</div>
  <div class="abs account"><span>REGISTER</span><span>|</span><span>LOGIN</span><span class="fl-login"><i></i>Login</span></div>
  <nav class="abs mainnav"><span>HOME</span><span>ABOUT US</span><span>PROPERTIES</span><span>CONTACT US</span></nav>
</header>

<div class="abs panel"></div>

<aside>
  <div class="abs sidebar"></div>
  <div class="abs map" role="img" aria-label="Road map of the search area with a numbered property marker"></div>
  <div class="abs side-rule" style="top:348px"></div>
  <div class="abs side-label" style="top:361px">REFINE SEARCH</div>
  <div class="abs select" style="left:122px;top:386px;width:181px">For Sale<svg viewBox="0 0 10 9"><path d="M0 0h10L5 9z" fill="#111"/></svg></div>
  <div class="abs select" style="left:122px;top:418px;width:181px">Property Type<svg viewBox="0 0 10 9"><path d="M0 0h10L5 9z" fill="#111"/></svg></div>
  <div class="abs select" style="left:122px;top:451px;width:87px">Min Price<svg viewBox="0 0 10 9"><path d="M0 0h10L5 9z" fill="#111"/></svg></div>
  <div class="abs select" style="left:216px;top:451px;width:87px">Max Price<svg viewBox="0 0 10 9"><path d="M0 0h10L5 9z" fill="#111"/></svg></div>
  <div class="abs select" style="left:122px;top:483px;width:87px">Beds<svg viewBox="0 0 10 9"><path d="M0 0h10L5 9z" fill="#111"/></svg></div>
  <div class="abs select" style="left:216px;top:483px;width:87px">Baths<svg viewBox="0 0 10 9"><path d="M0 0h10L5 9z" fill="#111"/></svg></div>
  <div class="abs select" style="left:122px;top:516px;width:87px">Min Size<svg viewBox="0 0 10 9"><path d="M0 0h10L5 9z" fill="#111"/></svg></div>
  <div class="abs select" style="left:216px;top:516px;width:87px">Max Size<svg viewBox="0 0 10 9"><path d="M0 0h10L5 9z" fill="#111"/></svg></div>
  <div class="abs btn-black" style="top:549px">update</div>
  <div class="abs side-rule" style="top:585px"></div>
  <div class="abs side-label" style="top:598px">NEIGHBORHOOD</div>
  <ul class="abs hoods">
    <li><span class="box"></span>Frostproof</li>
    <li><span class="box"><svg width="7" height="6" viewBox="0 0 7 6"><path d="M0.5 3l2 2 4-4.5" stroke="#2c7a2c" stroke-width="1.4" fill="none"/></svg></span>Bowling Green</li>
    <li><span class="box"></span>Avon Park</li>
    <li><span class="box"><svg width="7" height="6" viewBox="0 0 7 6"><path d="M0.5 3l2 2 4-4.5" stroke="#2c7a2c" stroke-width="1.4" fill="none"/></svg></span>Hillcrest Heights</li>
    <li><span class="box"></span>Bartow</li>
    <li><span class="box"></span>Waverly</li>
  </ul>
  <div class="abs btn-black" style="top:724px">view all</div>
</aside>

<main>
  <div class="abs toolbar" style="top:145px">Sort By<span class="tb-select" style="width:92px">Most Recent<b></b></span>Per Page<span class="tb-select" style="width:36px">4<b></b></span>
    <span class="pager"><svg viewBox="0 0 8 11"><path d="M7 1L2 5.5 7 10" stroke="#d3ac62" stroke-width="2.4" fill="none"/></svg>Page&nbsp;&nbsp;1 | <b>2</b> | 3<svg viewBox="0 0 8 11"><path d="M1 1l5 4.5L1 10" stroke="#d3ac62" stroke-width="2.4" fill="none"/></svg></span></div>

  <article class="abs listing" style="top:192px">
    <div class="photo" role="img" aria-label="Bright bedroom with a dark wood bed and city-view windows"></div>
    <h2 class="title" style="font-weight:400">Lorem Ipsum is simply dummy text</h2>
    <div class="price">$985,000</div>
    <div class="addr">1180 Harbor Crest Ave, Tampa, Florida, 33611</div>
    <p class="desc">Lorem Ipsum is simply dummy text of the printing and typesetting industry. Lorem Ipsum has been the industry's standard dummy text ever since the 1500s, when an unknown printer took a galley of type and scrambled it to make a type specimen book.</p>
    <div class="badges">
      <span class="badge">3<svg viewBox="0 0 24 10"><path d="M1 1v8M1 6h22v3M4 3h6v3M23 4v5" stroke="#fff" stroke-width="1.6" fill="none"/></svg></span>
      <span class="badge">3<svg viewBox="0 0 24 10"><path d="M1 1v4h22l-2 4H4L1 5" stroke="#fff" stroke-width="1.6" fill="none"/></svg></span>
      <span class="badge">4<svg viewBox="0 0 24 10"><path d="M1 7h22V5l-5-1-3-3H8L5 4 1 5z" fill="#fff"/><circle cx="6" cy="8" r="1.6" fill="#d3ac62"/><circle cx="18" cy="8" r="1.6" fill="#d3ac62"/></svg></span>
      <span class="badge view">view</span>
    </div>
  </article>

  <article class="abs listing" style="top:363px">
    <div class="photo" role="img" aria-label="Bright bedroom with a dark wood bed and city-view windows"></div>
    <h2 class="title" style="font-weight:400">Lorem Ipsum is simply dummy text</h2>
    <div class="price">$985,000</div>
    <div class="addr">1180 Harbor Crest Ave, Tampa, Florida, 33611</div>
    <p class="desc">Lorem Ipsum is simply dummy text of the printing and typesetting industry. Lorem Ipsum has been the industry's standard dummy text ever since the 1500s, when an unknown printer took a galley of type and scrambled it to make a type specimen book.</p>
    <div class="badges">
      <span class="badge">3<svg viewBox="0 0 24 10"><path d="M1 1v8M1 6h22v3M4 3h6v3M23 4v5" stroke="#fff" stroke-width="1.6" fill="none"/></svg></span>
      <span class="badge">3<svg viewBox="0 0 24 10"><path d="M1 1v4h22l-2 4H4L1 5" stroke="#fff" stroke-width="1.6" fill="none"/></svg></span>
      <span class="badge">4<svg viewBox="0 0 24 10"><path d="M1 7h22V5l-5-1-3-3H8L5 4 1 5z" fill="#fff"/><circle cx="6" cy="8" r="1.6" fill="#d3ac62"/><circle cx="18" cy="8" r="1.6" fill="#d3ac62"/></svg></span>
      <span class="badge view">view</span>
    </div>
  </article>

  <article class="abs listing" style="top:534px">
    <div class="photo" role="img" aria-label="Bright bedroom with a dark wood bed and city-view windows"></div>
    <h2 class="title" style="font-weight:400">Lorem Ipsum is simply dummy text</h2>
    <div class="price">$985,000</div>
    <div class="addr">1180 Harbor Crest Ave, Tampa, Florida, 33611</div>
    <p class="desc">Lorem Ipsum is simply dummy text of the printing and typesetting industry. Lorem Ipsum has been the industry's standard dummy text ever since the 1500s, when an unknown printer took a galley of type and scrambled it to make a type specimen book.</p>
    <div class="badges">
      <span class="badge">3<svg viewBox="0 0 24 10"><path d="M1 1v8M1 6h22v3M4 3h6v3M23 4v5" stroke="#fff" stroke-width="1.6" fill="none"/></svg></span>
      <span class="badge">3<svg viewBox="0 0 24 10"><path d="M1 1v4h22l-2 4H4L1 5" stroke="#fff" stroke-width="1.6" fill="none"/></svg></span>
      <span class="badge">4<svg viewBox="0 0 24 10"><path d="M1 7h22V5l-5-1-3-3H8L5 4 1 5z" fill="#fff"/><circle cx="6" cy="8" r="1.6" fill="#d3ac62"/><circle cx="18" cy="8" r="1.6" fill="#d3ac62"/></svg></span>
      <span class="badge view">view</span>
    </div>
  </article>

  <article class="abs listing" style="top:705px;border-bottom:none">
    <div class="photo" role="img" aria-label="Bright bedroom with a dark wood bed and city-view windows"></div>
    <h2 class="title" style="font-weight:400">Lorem Ipsum is simply dummy text</h2>
    <div class="price">$985,000</div>
    <div class="addr">1180 Harbor Crest Ave, Tampa, Florida, 33611</div>
    <p class="desc">Lorem Ipsum is simply dummy text of the printing and typesetting industry. Lorem Ipsum has been the industry's standard dummy text ever since the 1500s, when an unknown printer took a galley of type and scrambled it to make a type specimen book.</p>
    <div class="badges">
      <span class="badge">3<svg viewBox="0 0 24 10"><path d="M1 1v8M1 6h22v3M4 3h6v3M23 4v5" stroke="#fff" stroke-width="1.6" fill="none"/></svg></span>
      <span class="badge">3<svg viewBox="0 0 24 10"><path d="M1 1v4h22l-2 4H4L1 5" stroke="#fff" stroke-width="1.6" fill="none"/></svg></span>
      <span class="badge">4<svg viewBox="0 0 24 10"><path d="M1 7h22V5l-5-1-3-3H8L5 4 1 5z" fill="#fff"/><circle cx="6" cy="8" r="1.6" fill="#d3ac62"/><circle cx="18" cy="8" r="1.6" fill="#d3ac62"/></svg></span>
      <span class="badge view">view</span>
    </div>
  </article>

  <div class="abs toolbar" style="top:875px">Sort By<span class="tb-select" style="width:92px">Most Recent<b></b></span>Per Page<span class="tb-select" style="width:36px">4<b></b></span>
    <span class="pager"><svg viewBox="0 0 8 11"><path d="M7 1L2 5.5 7 10" stroke="#d3ac62" stroke-width="2.4" fill="none"/></svg>Page&nbsp;&nbsp;1 | <b>2</b> | 3<svg viewBox="0 0 8 11"><path d="M1 1l5 4.5L1 10" stroke="#d3ac62" stroke-width="2.4" fill="none"/></svg></span></div>
</main>

<footer>
  <nav class="abs footnav"><span>CONTACT</span><span>ABOUT</span><span>SITEMAP</span><span>CAREERS</span><span>FRANCHISE OPPORTUNITIES</span><span>SELLER LOGIN</span></nav>
  <div class="abs social" style="left:790px">Friend<br>loop</div>
  <div class="abs social" style="left:828px">Link<br>well</div>
  <div class="abs social" style="left:865px">Chirp<br>line</div>
  <div class="abs social" style="left:903px">View<br>tube</div>
  <div class="abs rule" style="top:1033px"></div>

  <div class="abs fcol" style="left:88px">Nam at risus id ligula<br>Donec ut elit et<br>Donec quis nibh<br>Maecenas eu<br>Vestibulum a nulla.</div>
  <div class="abs fcol" style="left:260px">Nam at risus id ligula<br>Donec ut elit et<br>Donec quis nibh<br>Maecenas eu<br>Vestibulum a nulla.</div>

  <div class="abs news-title">Latest News</div>
  <svg class="abs arrow" style="left:418px" viewBox="0 0 9 12"><path d="M7 1L2 6l5 5" stroke="#6d747e" stroke-width="2" fill="none"/></svg>
  <div class="abs news-box">Lorem Ipsum is simply dummy text of the printing and...<br><span class="readmore">read more</span></div>
  <svg class="abs arrow" style="left:665px" viewBox="0 0 9 12"><path d="M2 1l5 5-5 5" stroke="#6d747e" stroke-width="2" fill="none"/></svg>

  <div class="abs nl-title">JOIN OUR NEWSLETTER</div>
  <div class="abs input" style="left:711px;top:1085px;width:107px">First Name</div>
  <div class="abs input" style="left:826px;top:1085px;width:107px">Last Name</div>
  <div class="abs input" style="left:711px;top:1118px;width:162px">Email</div>
  <div class="abs submit">Submit</div>

  <div class="abs rule short" style="top:1167px"></div>
  <div class="abs copy">Copyright © 2012 Lake Vorissa Real Estate</div>
</footer>
</body>
</html>
```